Tech business card design

We need an amazing business card design for our new business 'Pexla' a marketing tech startup based in Sydney, Australia. We provide an online marketplace for businesses to search and buy advertising media, connect with service providers and learn more about marketing. We wish to communicate 'cool tech', reliability and professionalism and design based around our logo.

Target Market(s)

Business Owners

Contact Information for Business Card

Name
Position
Email Address
Website
Phone Number

Font styles to use
Other font styles liked:
• Avenir & Avenir Next

Colors

Designer to choose colors to be used in the design.

```html
<!DOCTYPE html>
<html lang="en">
<head>
<meta charset="utf-8">
<title>Pexla Business Card</title>
<link rel="stylesheet" href="https://fonts.googleapis.com/css2?family=Source+Sans+3:wght@400;600;700;800&display=swap">
<style>
  :root {
    --backdrop: #e0dddd;
    --card-light: #ffffff;
    --card-dark: #3a3a3c;
    --navy: #161838;
    --ink: #231f20;
    --white: #ffffff;
    --edge: #d6d3d3;
  }
  * { margin: 0; padding: 0; box-sizing: border-box; }
  html, body {
    width: 975px; height: 1200px; overflow: hidden;
    background: var(--backdrop);
    font-family: "Source Sans 3", "Helvetica Neue", Arial, sans-serif;
  }
  .canvas { position: relative; width: 975px; height: 1200px; }
  .card { position: absolute; left: 59px; width: 858px; height: 491px; }
  .card--front { top: 67px; background: var(--card-light); border: 1px solid var(--edge); }
  .card--back { top: 633px; background: var(--card-dark); }

  .wordmark {
    position: absolute; font-weight: 800; line-height: 1;
    letter-spacing: -2px;
  }
  .card--front .wordmark { right: 110px; top: 48px; font-size: 150px; color: var(--navy); }
  .card--back .wordmark { left: 0; right: 0; text-align: center; top: 180px; font-size: 160px; color: var(--white); }

  .holder { position: absolute; left: 58px; top: 221px; }
  .holder__name { font-size: 29px; font-weight: 700; color: var(--ink); line-height: 1.1; letter-spacing: 0.2px; }
  .holder__position { font-size: 25px; font-weight: 400; color: var(--ink); line-height: 1.3; }
  .divider { position: absolute; left: 58px; top: 293px; width: 734px; height: 2px; background: var(--navy); }

  .contacts { position: absolute; left: 58px; top: 326px; list-style: none; }
  .contacts li { display: flex; align-items: center; height: 36.5px; font-size: 22px; color: var(--ink); }
  .contacts svg { width: 20px; height: 20px; margin-right: 9px; flex: none; }
  .contacts .web { letter-spacing: 2px; }

  .address {
    position: absolute; right: 66px; top: 348px; text-align: right;
    font-size: 22px; line-height: 29px; color: var(--ink); font-style: normal;
  }
  .back-url {
    position: absolute; left: 0; right: 0; top: 404px; text-align: center;
    font-size: 29px; letter-spacing: 3.5px; color: var(--white); padding-right: 30px;
  }
</style>
</head>
<body>
<main class="canvas">
  <section class="card card--front">
    <div class="wordmark">pexla</div>
    <div class="holder">
      <p class="holder__name">JOHN SMITH</p>
      <p class="holder__position">Position</p>
    </div>
    <div class="divider"></div>
    <ul class="contacts">
      <li>
        <svg viewBox="0 0 20 20" aria-hidden="true"><circle cx="10" cy="10" r="8.8" fill="none" stroke="#231f20" stroke-width="1.4"/><path d="M7 5.5c-1 1-1.2 3 .3 5.5s3.6 4 5 3.6l1-1.2-1.8-1.6-1 .7c-.8-.3-2-1.8-2.4-2.8l.8-.9-1-2.2z" fill="#231f20"/></svg>
        012-345-6789
      </li>
      <li>
        <svg viewBox="0 0 20 20" aria-hidden="true"><rect x="1" y="4" width="18" height="12" fill="#231f20"/><path d="M1.5 4.5L10 11l8.5-6.5M1.5 15.5l6-5.5M18.5 15.5l-6-5.5" stroke="#fff" stroke-width="1.3" fill="none"/></svg>
        info@pexla.com
      </li>
      <li class="web">
        <svg viewBox="0 0 20 20" aria-hidden="true"><g fill="none" stroke="#231f20" stroke-width="1.3"><circle cx="10" cy="10" r="8.5"/><ellipse cx="10" cy="10" rx="3.8" ry="8.5"/><path d="M1.5 10h17M3 5.5h14M3 14.5h14M10 1.5v17"/></g></svg>
        www.pexla.com
      </li>
    </ul>
    <address class="address">Street name City Name,<br>Zipcode,012345</address>
  </section>

  <section class="card card--back">
    <div class="wordmark">pexla</div>
    <p class="back-url">www.pexla.com</p>
  </section>
</main>
</body>
</html>
```